Box for a Bold Bathroom - stylish minimalist package for a modern upscale brand

We need an adaptable package design using a color label on a brown box, or just a brown box with 2 or 3 color printing. The best design would be one that is adaptable for either use.

Our first products launching under this brand will be a series of medicine cabinets and mirrors, and our cartons can vary in size from 500x100x600 mm to 1200x300x1000 mm

About us: we produce a variety of bathroom fixtures including medicine cabinets, mirrors, vanities, etc. You've likely seen our products - we do manufacturing for Brantley, Marlowe, Thistle Cove, Dunmore & Pike, and others.

A version of our logo is attached for reference; we use it in a variety of color mixes depending on application. Vector available if needed or can be used FPO and our team will replace.

These are our colors, please take note and ignore the 'color' field:

Light Blue: C:66%/M:6%/Y:22%/K:0%; H:189° S:65% B:78%
Light Grey: C:35%/M:26%/Y:24%/K:0%; H:213° S:5% B:70%
Dark Blue: C:90%/M:50%/Y:44%/K:20%; H:189° S:82% B:43%
Dark Grey: C:70%/M:60%/Y:54%/K:38%; H:213° S:11% B:30%

Reason: Some revisions still outstanding before we can make selection, and some submissions we have agreed to wait for. Please submit all work ASAP so our team can provide feedback to you. Thanks!

Target Market(s)

DIY'ers; home renovators

Industry/Entity Type

Home Improvement

Font styles to use
Sans Serif

Requirements
Must have
• 1. Brand logo w/ logotype
• 2. Brand name without logo (can be on shipping mark side)
• 3. Multi-lingual En/Fr/Es (you do not need to include multi-lingual content but must allow space for our own translations if you do not)
• 4. Shipping/Handling Glyphs on 5 sides (all but bottom)
• i.e. fragile, this way up, team lift or mech lift, clamp or no clamp, max-stack
• 5. Two sides should include a marked 4" x 4" area for affixing labels (e.g. UPC, SSCC, etc.) ideally with a dotted line or corner marks or similar.
• 6. Shipping mark details or space for them (should be on the smallest side, only needed on one but can be on both) [see example file of shipping mark informations]
Nice to have
• Design that can be used either with color label on brown box, or brown box only.
• If designing for color label; please see the sample images included. Lifestyle should be prominent, the inside photo being smaller to help show interior features. These photos are obviously not useful for brown-box design.

```html
<!DOCTYPE html>
<html lang="en">
<head>
<meta charset="utf-8">
<title>Clearwell Carton Dieline</title>
<link rel="stylesheet" href="https://fonts.googleapis.com/css2?family=Montserrat:wght@500;700&family=Oswald:wght@500&display=swap">
<style>
  :root {
    --backdrop: #e6e7e9;
    --kraft: #bf9270;
    --kraft-flap: #c9a07e;
    --cut-line: #3b3a3a;
    --dark-blue: #17606e;
    --dark-grey: #43464b;
    --light-blue: #2ec4d6;
    --label-white: #ffffff;
  }
  html, body {
    margin: 0;
    padding: 0;
    width: 1200px;
    height: 1200px;
    overflow: hidden;
    background: var(--backdrop);
  }
  .dieline { display: block; width: 1200px; height: 1200px; }
  .panel { fill: var(--kraft); stroke: var(--cut-line); stroke-width: 1; }
  .flap-light { fill: var(--kraft-flap); stroke: var(--cut-line); stroke-width: 1; }
  .band-blue { fill: var(--dark-blue); }
  .brand-name {
    font-family: "Montserrat", sans-serif;
    font-weight: 500;
    fill: var(--dark-grey);
    letter-spacing: 2px;
  }
  .brand-dot { fill: var(--light-blue); }
  .icon-frame { fill: none; stroke: var(--dark-grey); stroke-width: 1.5; }
  .icon-ink { fill: none; stroke: var(--dark-grey); stroke-width: 2.5; stroke-linecap: round; stroke-linejoin: round; }
  .icon-fill { fill: var(--dark-grey); }
  .label-card { fill: var(--label-white); }
  .label-rule { stroke: var(--dark-grey); stroke-width: 0.6; }
  .label-text {
    font-family: "Oswald", sans-serif;
    font-weight: 500;
    font-size: 4.2px;
    fill: var(--dark-grey);
  }
  .label-zone { fill: none; stroke: var(--dark-grey); stroke-width: 1; stroke-dasharray: 2 1.5; }
</style>
</head>
<body>
<svg class="dieline" viewBox="0 0 1500 1500" xmlns="http://www.w3.org/2000/svg">
  <defs>
    <linearGradient id="chevron-tone" x1="0" x2="1" y1="0" y2="0">
      <stop offset="0" stop-color="#17606e"/>
      <stop offset="0.5" stop-color="#43464b"/>
      <stop offset="1" stop-color="#17606e"/>
    </linearGradient>

    <symbol id="shipping-label" viewBox="0 0 110 81">
      <rect class="label-card" width="110" height="81"/>
      <line class="label-rule" x1="0" y1="33" x2="110" y2="33"/>
      <line class="label-rule" x1="53" y1="0" x2="53" y2="33"/>
      <line class="label-rule" x1="0" y1="17" x2="53" y2="17"/>
      <text class="label-text" x="4" y="8">LOT# 000000</text>
      <text class="label-text" x="4" y="13">ITEM# 0000000</text>
      <text class="label-text" x="3" y="24">DIM 00x00x00 CM</text>
      <text class="label-text" x="57" y="12">NW/PK 0 KG</text>
      <text class="label-text" x="57" y="18">GW/PK 0 KG</text>
      <text class="label-text" x="57" y="24">ORIGIN CN</text>
      <text class="label-text" x="3" y="40">QTY 1</text>
      <text class="label-text" x="3" y="47">CASE</text>
      <rect class="label-zone" x="66" y="40" width="36" height="36"/>
    </symbol>

    <symbol id="icon-recycle" viewBox="0 0 38 38">
      <rect class="icon-frame" x="0.75" y="0.75" width="36.5" height="36.5"/>
      <path class="icon-ink" d="M12 24 A8 8 0 0 1 19 11 M26 16 A8 8 0 0 1 22 27 M15 27 L12 24 L15 21 M16 10 L19 11 L18 14 M22 27 L26 27 L25 24"/>
    </symbol>
    <symbol id="icon-upright" viewBox="0 0 38 38">
      <rect class="icon-frame" x="0.75" y="0.75" width="36.5" height="36.5"/>
      <path class="icon-ink" d="M14 28 V10 M9 15 L14 10 L19 15 M24 28 V10 M19 15 L24 10 L29 15 M8 31 H30"/>
    </symbol>
    <symbol id="icon-keep-dry" viewBox="0 0 38 38">
      <rect class="icon-frame" x="0.75" y="0.75" width="36.5" height="36.5"/>
      <path class="icon-fill" d="M7 20 A12 11 0 0 1 31 20 Z"/>
      <path class="icon-ink" d="M19 20 V29 A2.5 2.5 0 0 1 14 29"/>
    </symbol>
    <symbol id="icon-fragile" viewBox="0 0 38 38">
      <rect class="icon-frame" x="0.75" y="0.75" width="36.5" height="36.5"/>
      <path class="icon-fill" d="M9 8 H23 V16 A7 7 0 0 1 9 16 Z"/>
      <path class="icon-ink" d="M16 23 V30 M11 30 H21 M27 16 V30 M24 30 H30"/>
    </symbol>
    <symbol id="icon-handle-care" viewBox="0 0 38 38">
      <rect class="icon-frame" x="0.75" y="0.75" width="36.5" height="36.5"/>
      <rect class="icon-fill" x="13" y="12" width="12" height="12"/>
      <path class="icon-ink" d="M6 8 L11 14 L11 20 M32 30 L27 24 L27 18 M6 30 L11 24 M32 8 L27 14"/>
    </symbol>
  </defs>

  <!-- ===== Upper dieline ===== -->
  <g class="dieline-upper">
    <rect class="panel" x="541" y="22" width="417" height="26"/>
    <rect class="panel" x="540" y="48" width="420" height="142"/>
    <g class="brand-lockup" transform="rotate(180 750 118)">
      <circle class="brand-dot" cx="750" cy="102" r="7"/>
      <text class="brand-name" x="750" y="124" font-size="15" text-anchor="middle">CLEARWELL</text>
    </g>

    <polygon class="flap-light" points="508,197 540,190 540,686 508,680"/>

    <rect class="panel" x="540" y="190" width="420" height="496"/>
    <g class="brand-lockup">
      <circle class="brand-dot" cx="750" cy="420" r="16"/>
      <text class="brand-name" x="750" y="468" font-size="17" text-anchor="middle">CLEARWELL</text>
    </g>
    <rect x="540" y="576" width="420" height="72" fill="url(#chevron-tone)" role="img" aria-label="Chevron band in dark blue and dark grey"/>
    <rect class="band-blue" x="540" y="676" width="420" height="10"/>

    <rect class="panel" x="540" y="686" width="420" height="70"/>
    <rect class="panel" x="540" y="756" width="70" height="19" rx="4"/>
    <rect class="panel" x="890" y="756" width="70" height="19" rx="4"/>

    <polygon class="panel" points="963,104 1085,104 1093,170 1100,190 960,190"/>
    <rect class="panel" x="960" y="190" width="140" height="496"/>
    <text class="brand-name" font-size="14" text-anchor="middle" transform="translate(989 283) rotate(-90)">CLEARWELL</text>
    <use href="#icon-recycle" x="1047" y="205" width="38" height="38"/>
    <use href="#icon-upright" x="1047" y="247" width="38" height="38"/>
    <use href="#icon-keep-dry" x="1047" y="289" width="38" height="38"/>
    <use href="#icon-fragile" x="1047" y="331" width="38" height="38"/>
    <use href="#icon-handle-care" x="1047" y="373" width="38" height="38"/>
    <rect class="band-blue" x="1046" y="427" width="38" height="259"/>
    <use href="#shipping-label" x="975" y="583" width="110" height="81"/>

    <path class="panel" d="M960,686 H1100 V772 H1045 L1030,758 A8 8 0 0 0 1020,772 H1045 Z"/>
  </g>

  <!-- ===== Lower dieline ===== -->
  <g class="dieline-lower">
    <path class="panel" d="M400,895 L477,818 L462,818 A8 8 0 0 0 462,828 L477,818 L485,810 H540 V895 Z"/>
    <rect class="panel" x="400" y="895" width="140" height="495"/>
    <use href="#shipping-label" x="415" y="917" width="110" height="81" transform="rotate(180 470 957.5)"/>
    <rect class="band-blue" x="415" y="998" width="38" height="157"/>
    <use href="#icon-handle-care" x="415" y="1171" width="38" height="38"/>
    <use href="#icon-fragile" x="415" y="1213" width="38" height="38"/>
    <use href="#icon-keep-dry" x="415" y="1255" width="38" height="38"/>
    <use href="#icon-upright" x="415" y="1297" width="38" height="38"/>
    <use href="#icon-recycle" x="415" y="1339" width="38" height="38"/>
    <text class="brand-name" font-size="14" text-anchor="middle" transform="translate(511 1296) rotate(90)">CLEARWELL</text>
    <polygon class="panel" points="400,1390 540,1390 525,1477 400,1477"/>

    <rect class="panel" x="610" y="805" width="280" height="22" rx="6"/>
    <polygon class="panel" points="540,895 632,825 890,825 960,895"/>

    <rect class="panel" x="540" y="895" width="420" height="495"/>
    <rect class="band-blue" x="540" y="897" width="420" height="8"/>
    <rect x="540" y="937" width="420" height="71" fill="url(#chevron-tone)" role="img" aria-label="Chevron band in dark blue and dark grey"/>
    <g class="brand-lockup" transform="rotate(180 750 1130)">
      <circle class="brand-dot" cx="750" cy="1110" r="16"/>
      <text class="brand-name" x="750" y="1158" font-size="17" text-anchor="middle">CLEARWELL</text>
    </g>

    <polygon class="flap-light" points="960,895 993,900 993,1385 960,1390"/>
    <rect class="flap-light" x="716" y="1360" width="67" height="60" rx="5"/>
  </g>
</svg>
</body>
</html>
```